LHP Regal Business Card Design 2020

Your Manor Steward is looking for a business card that is clean and straight to the point but still looks high-end and attractive. We are a team comprised of management and field professionals focused on the high-end residential marketplace. We serve homeowners and trade professionals directly based out of the Metrowest/Boston area. We provide client services as well as construction/renovation services.
We are aiming for a black and white feel (white background and black text) and a matte finish with rounded edges.

We want to emphasis our vision of "Properties - Projects - Partners".
Dana Pellham is the president of LHP

Please include the following areas we service: Boston/Cape/Newport
Please make sure to include Dana's mobile (555) 213 4480 & office number (555) 640 1937, email dana@yourmanorsteward.example and website www.yourmanorsteward.example

Colors

Designer to choose only greyscale colors for use in the design.

Requirements
Must have
• Include "Properties - Projects - Partners" in design

Include "After Hours Emergency Support # 1800 555 0142" with icon

```html
<!DOCTYPE html>
<html lang="en">
<head>
<meta charset="utf-8">
<title>LHP Business Card</title>
<link rel="stylesheet" href="https://fonts.googleapis.com/css2?family=Poppins:wght@400;500;700&display=swap">
<style>
  :root {
    --backdrop: #222222;
    --card: #ffffff;
    --ink: #1f1f1f;
    --band: #262626;
    --band-text: #f2f2f2;
    --rule: #2a2a2a;
  }
  * { margin: 0; padding: 0; box-sizing: border-box; }
  html, body { width: 1200px; height: 1200px; overflow: hidden; }
  body {
    background: var(--backdrop);
    font-family: "Poppins", sans-serif;
    color: var(--ink);
    display: flex;
    flex-direction: column;
    align-items: center;
    justify-content: center;
    gap: 60px;
  }
  .card {
    position: relative;
    width: 880px;
    height: 490px;
    background: var(--card);
    border-radius: 12px;
    overflow: hidden;
  }
  .band {
    position: absolute;
    left: 0; right: 0;
    top: 356px;
    height: 72px;
    background: var(--band);
    color: var(--band-text);
    display: flex;
    align-items: center;
    justify-content: center;
  }
  .wordmark {
    display: flex;
    flex-direction: column;
    align-items: center;
    font-weight: 700;
    color: var(--ink);
  }
  .wordmark-initials { font-size: 150px; line-height: 1; letter-spacing: -2px; }
  .wordmark-name { font-size: 24px; letter-spacing: 3px; text-transform: uppercase; margin-top: 6px; }

  /* front */
  .card-front .wordmark { position: absolute; left: 0; right: 0; top: 90px; }
  .vision { font-size: 24px; letter-spacing: 7px; text-transform: uppercase; font-weight: 400; }

  /* back */
  .card-back .wordmark { position: absolute; left: 30px; width: 370px; top: 84px; }
  .card-back .wordmark-initials { font-size: 136px; }
  .card-back .wordmark-name { font-size: 21px; letter-spacing: 2.5px; }
  .divider {
    position: absolute;
    left: 420px; top: 64px;
    width: 2px; height: 260px;
    background: var(--rule);
  }
  .contact { position: absolute; left: 452px; right: 24px; top: 70px; }
  .contact-name { font-size: 28px; font-weight: 700; text-transform: uppercase; letter-spacing: 1px; line-height: 1.1; }
  .contact-role { font-size: 20px; font-weight: 400; margin-bottom: 18px; }
  .contact-list { list-style: none; }
  .contact-list li { display: flex; align-items: center; gap: 12px; font-size: 18px; line-height: 1.55; white-space: nowrap; }
  .contact-list svg, .emergency svg { width: 20px; height: 20px; flex: none; }
  .areas { font-size: 26px; letter-spacing: 2px; font-weight: 400; }
  .emergency {
    position: absolute;
    left: 0; right: 0;
    top: 428px; height: 62px;
    display: flex;
    align-items: center;
    justify-content: center;
    gap: 10px;
    font-size: 18px;
    font-weight: 500;
  }
</style>
</head>
<body>

<section class="card card-front">
  <div class="wordmark">
    <span class="wordmark-initials">LHP</span>
    <span class="wordmark-name">Your Manor Steward</span>
  </div>
  <div class="band"><p class="vision">Properties – Projects – Partners</p></div>
</section>

<section class="card card-back">
  <div class="wordmark">
    <span class="wordmark-initials">LHP</span>
    <span class="wordmark-name">Your Manor Steward</span>
  </div>
  <div class="divider"></div>
  <div class="contact">
    <p class="contact-name">Dana Pellham</p>
    <p class="contact-role">President of LHP</p>
    <ul class="contact-list">
      <li>
        <svg viewBox="0 0 24 24" fill="none" stroke="currentColor" stroke-width="2"><rect x="5" y="3" width="14" height="18" rx="1"/><line x1="10" y1="18" x2="14" y2="18"/></svg>
        (555) 213 4480
      </li>
      <li>
        <svg viewBox="0 0 24 24" fill="currentColor"><path d="M3 9c0-3 4-5 9-5s9 2 9 5l-4 1-1-2c-2-.6-6-.6-8 0l-1 2z"/><rect x="6" y="12" width="12" height="8" rx="1"/></svg>
        (555) 640 1937
      </li>
      <li>
        <svg viewBox="0 0 24 24" fill="currentColor"><path d="M2 5h20v14H2z"/><path d="M2 5l10 8 10-8" fill="none" stroke="#fff" stroke-width="1.6"/></svg>
        dana@yourmanorsteward.example
      </li>
      <li>
        <svg viewBox="0 0 24 24" fill="none" stroke="currentColor" stroke-width="1.6"><circle cx="12" cy="12" r="9"/><ellipse cx="12" cy="12" rx="4" ry="9"/><line x1="3" y1="12" x2="21" y2="12"/><line x1="5" y1="7" x2="19" y2="7"/><line x1="5" y1="17" x2="19" y2="17"/></svg>
        www.yourmanorsteward.example
      </li>
    </ul>
  </div>
  <div class="band"><p class="areas">Boston | Metrowest | South Shore | Cape | Newport</p></div>
  <p class="emergency">
    <svg viewBox="0 0 24 24" fill="currentColor"><path d="M6.6 10.8a15 15 0 0 0 6.6 6.6l2.2-2.2a1 1 0 0 1 1-.25 11.4 11.4 0 0 0 3.6.57 1 1 0 0 1 1 1V20a1 1 0 0 1-1 1A17 17 0 0 1 3 4a1 1 0 0 1 1-1h3.5a1 1 0 0 1 1 1c0 1.25.2 2.45.57 3.6a1 1 0 0 1-.25 1z"/></svg>
    After Hours Emergency Support # 1800 555 0142
  </p>
</section>

</body>
</html>
```